Stylish High End Wedding Videography/Films Website (BMRT)

We need a modern and high-end website look for our wedding video and films business. We films weddings all over the United Kingdom and at European destinations so need something to reflect our work. The website should be visually stunning with images and videos being the focal point as this is what our services are;

I have uploads of some items I like and the features the site needs to have. These have been taken from other websites using standout features.

We need the following pages;

1 - Homepage
2 - Films Index Page
3 - Individual Films Page
4 - Prices / Collection Page
5 - Reviews
6 - Options
7 - About
8 - Contact
9 - Blog Index
10 - Blog Page

All pages must be consistent so have a similar style.

Pages on menu:
Films
Prices
Reviews
Options
About
Contact

We require a responsive look too. Over 90% of our visitors access the website via their mobile devices.

Please use the colours from our logo to incorporate into the website.

Target Market(s)

Wedding Couples

Industry/Entity Type

Wedding Photography

Number of Pages Required

5+ page

Font styles to use
Sans Serif
Script

Requirements
Must have
• The logo must be in the centre of the menu at the top.

Social icons at the bottom of the page.

Use only two fonts including Lore which is supplied
Nice to have
• Different video for each page on the top header. This will play behind the menu.

```html
<!DOCTYPE html>
<html lang="en">
<head>
<meta charset="utf-8">
<title>BMRT Wedding Films – Wedding Film Portfolio</title>
<link href="https://fonts.googleapis.com/css2?family=Montserrat:wght@400;500;600;700&display=swap" rel="stylesheet">
<style>
:root{
  --gold:#a38d58;
  --gold-band:#a08b55;
  --ink:#1f1d1e;
  --text:#3b3b3b;
  --muted:#8a8a8a;
  --soft:#f5f5f5;
  --footer:#242022;
  --white:#ffffff;
}
*{margin:0;padding:0;box-sizing:border-box}
html,body{width:1200px;height:4490px;overflow:hidden}
body{position:relative;background:var(--white);font-family:'Montserrat',sans-serif;color:var(--text)}
.abs{position:absolute}

/* header */
.hero{left:0;top:0;width:1200px;height:459px;
  background:
    radial-gradient(ellipse 120px 170px at 610px 330px,rgba(238,236,230,.85),rgba(238,236,230,0) 100%),
    radial-gradient(ellipse 70px 140px at 560px 280px,rgba(30,30,32,.7),rgba(30,30,32,0) 100%),
    radial-gradient(ellipse 300px 120px at 230px 210px,rgba(38,52,34,.9),rgba(38,52,34,0) 100%),
    radial-gradient(ellipse 300px 160px at 1000px 220px,rgba(34,44,32,.95),rgba(34,44,32,0) 100%),
    radial-gradient(ellipse 160px 90px at 90px 380px,rgba(215,212,205,.8),rgba(215,212,205,0) 100%),
    radial-gradient(ellipse 220px 110px at 1100px 400px,rgba(120,110,100,.7),rgba(120,110,100,0) 100%),
    linear-gradient(180deg,#1a1d20 0%,#252b2d 22%,#3a4536 38%,#7c8449 55%,#9a9a5e 70%,#8a7a5a 85%,#5c5044 100%)}
.nav{top:101px;font-size:11px;letter-spacing:2px;color:var(--white);font-weight:500;display:flex;align-items:center}
.nav a{color:inherit;text-decoration:none}
.nav .active{color:var(--gold)}
.nav .dot{width:4px;height:4px;border-radius:50%;background:var(--white);margin:0 22px}
.brand{left:450px;width:300px;top:42px;text-align:center;color:var(--white)}
.brand .mark{width:30px;height:30px;border-radius:50%;border:2px solid var(--gold);margin:0 auto 20px}
.brand .name{font-size:19px;font-weight:600;letter-spacing:4px;line-height:1}
.brand .tag{font-size:8px;letter-spacing:4px;margin-top:6px;font-weight:500}

/* portfolio */
.section-title{left:0;width:1200px;top:543px;text-align:center;font-size:27px;font-weight:700;color:var(--ink)}
.film{left:268px;width:665px;height:458px;box-shadow:0 20px 40px rgba(0,0,0,.08)}
.film .play{position:absolute;left:50%;top:50%;width:76px;height:76px;margin:-38px 0 0 -38px}
.film-label{width:458px;height:60px;transform-origin:0 0;transform:rotate(-90deg);display:flex;align-items:baseline;gap:14px;white-space:nowrap}
.film-label .num{font-size:15px;color:var(--gold);font-weight:500}
.film-label .couple{font-size:15px;font-weight:600;color:var(--ink)}
.film-label .couple.gold{color:var(--gold)}
.film-label .venue{font-size:11px;color:var(--muted);display:block}
.film-label .names{display:flex;flex-direction:column;gap:6px;margin-left:24px}
.load-more{left:0;width:1200px;top:3136px;text-align:center;font-size:9px;letter-spacing:2px;font-weight:700;color:var(--ink)}
.load-more span{border-left:2px solid var(--gold);padding-left:14px}

/* testimonial */
.testimonial{left:0;top:3247px;width:1200px;height:375px;background:var(--soft)}
.quote{left:240px;width:720px;top:3336px;text-align:center;font-size:14.5px;line-height:31px;color:#666}
.quote .q{color:var(--gold);font-size:12px}
.avatar{left:570px;top:3461px;width:60px;height:60px;border-radius:50%;background:radial-gradient(circle at 40% 40%,#d9cbbb,#8a7866 55%,#3f3834)}
.arrow{top:3483px}
.reviewer{left:0;width:1200px;top:3536px;text-align:center;font-size:10px;letter-spacing:2.5px;font-weight:600;color:var(--ink)}

/* feature */
.feature-media{left:153px;top:3714px;width:447px;height:283px;
  background:
    radial-gradient(ellipse 60px 130px at 270px 150px,rgba(240,234,224,.9),rgba(240,234,224,0) 100%),
    radial-gradient(ellipse 60px 120px at 175px 160px,rgba(110,70,45,.85),rgba(110,70,45,0) 100%),
    radial-gradient(ellipse 200px 60px at 220px 270px,rgba(140,60,50,.6),rgba(140,60,50,0) 100%),
    linear-gradient(180deg,#c4c6c3 0%,#bfb29b 40%,#a68a66 70%,#8e7255 100%)}
.feature-title{left:677px;top:3750px;font-size:26px;font-weight:700;line-height:36px;color:var(--ink)}
.feature-text{left:677px;top:3838px;width:340px;font-size:10.5px;line-height:20px;color:#888}
.feature-link{left:677px;top:3938px;font-size:9px;letter-spacing:2px;font-weight:700;color:var(--ink);border-left:2px solid var(--gold);padding-left:22px;line-height:16px}

/* call to action */
.cta{left:0;top:4090px;width:1200px;height:151px;background:var(--gold-band)}
.cta-text{left:293px;top:4148px;font-size:25px;font-weight:700;color:var(--ink)}
.cta-btn{left:689px;top:4140px;width:192px;height:47px;background:var(--footer);color:var(--gold);font-size:11px;font-weight:600;display:flex;align-items:center;justify-content:center}

/* footer */
.footer{left:0;top:4241px;width:1200px;height:249px;background:var(--footer)}
.footer-brand{left:157px;top:4316px;font-size:34px;font-weight:700;letter-spacing:4px;color:var(--gold)}
.f-head{font-size:10px;letter-spacing:2.5px;font-weight:600;color:var(--white)}
.f-main{font-size:15px;font-weight:500;color:#e6e6e6;margin-top:14px}
.f-main .hl{color:var(--gold)}
.f-sub{font-size:11px;color:#9a9a9a;margin-top:6px}
.badge{left:986px;top:4306px;width:56px;height:56px;border-radius:50%;background:#f1dc66;border:3px solid #d4bf4a}
.divider{left:75px;top:4432px;width:1050px;height:1px;background:#3d383a}
.copyright{left:153px;top:4455px;font-size:10px;color:#9a9a9a}
.social{top:4447px;width:30px;height:30px;border-radius:50%;background:#4a4547}
</style>
</head>
<body>

<header>
  <div class="abs hero" role="img" aria-label="Header video still of a couple kissing in a meadow under falling confetti, pine trees behind and guests around them"></div>
  <nav class="abs nav" style="left:175px">
    <a class="active" href="#">FILMS</a><span class="dot"></span>
    <a href="#">PRICES</a><span class="dot"></span>
    <a href="#">REVIEWS</a>
  </nav>
  <div class="abs brand">
    <div class="mark"></div>
    <div class="name">BMRT</div>
    <div class="tag">WEDDING FILMS</div>
  </div>
  <nav class="abs nav" style="left:764px">
    <a href="#">OPTIONS</a><span class="dot"></span>
    <a href="#">ABOUT</a><span class="dot"></span>
    <a href="#">CONTACT</a>
  </nav>
</header>

<main>
  <h1 class="abs section-title">Wedding Film Portfolio</h1>

  <div class="abs film" style="top:617px;background:
    radial-gradient(ellipse 90px 200px at 300px 320px,rgba(236,232,226,.9),rgba(236,232,226,0) 100%),
    radial-gradient(ellipse 90px 220px at 400px 300px,rgba(70,72,70,.85),rgba(70,72,70,0) 100%),
    radial-gradient(ellipse 120px 230px at 110px 300px,rgba(70,90,75,.7),rgba(70,90,75,0) 100%),
    radial-gradient(ellipse 120px 230px at 580px 320px,rgba(190,175,160,.8),rgba(190,175,160,0) 100%),
    linear-gradient(180deg,#aeb1ae 0%,#8f8a80 40%,#6c665c 100%)" role="img" aria-label="Film still: couple walking through guests throwing confetti">
    <svg class="play" viewBox="0 0 76 76"><circle cx="38" cy="38" r="38" fill="rgba(255,255,255,.18)"/><path d="M31 25 L52 38 L31 51 Z" fill="none" stroke="#fff" stroke-width="2"/></svg>
  </div>
  <div class="abs film-label" style="left:190px;top:1075px">
    <span class="num">01.</span>
    <span class="names"><span class="couple gold">Ellie &amp; Marcus</span><span class="venue">Fernbrook Hall, Northumberland</span></span>
  </div>

  <div class="abs film" style="top:1121px;background:
    radial-gradient(ellipse 150px 170px at 160px 150px,rgba(232,238,222,.95),rgba(232,238,222,0) 100%),
    radial-gradient(ellipse 140px 150px at 360px 360px,rgba(38,62,110,.95),rgba(38,62,110,0) 100%),
    radial-gradient(ellipse 40px 110px at 480px 370px,rgba(226,170,60,.9),rgba(226,170,60,0) 100%),
    radial-gradient(ellipse 110px 170px at 440px 130px,rgba(205,150,115,.85),rgba(205,150,115,0) 100%),
    radial-gradient(ellipse 100px 200px at 610px 200px,rgba(236,200,170,.9),rgba(236,200,170,0) 100%),
    linear-gradient(120deg,#8fb06a 0%,#c8d6b4 35%,#e8e6de 70%,#f3ece4 100%)" role="img" aria-label="Film still: groom and bride touching foreheads beside a white bouquet">
    <svg class="play" viewBox="0 0 76 76"><circle cx="38" cy="38" r="38" fill="rgba(255,255,255,.18)"/><path d="M31 25 L52 38 L31 51 Z" fill="none" stroke="#fff" stroke-width="2"/></svg>
  </div>
  <div class="abs film-label" style="left:190px;top:1579px">
    <span class="num">02.</span>
    <span class="names"><span class="couple">Hattie &amp; Owen</span><span class="venue">Larchmere, Northumberland</span></span>
  </div>

  <div class="abs film" style="top:1625px;background:
    radial-gradient(ellipse 70px 200px at 280px 270px,rgba(120,80,50,.9),rgba(120,80,50,0) 100%),
    radial-gradient(ellipse 80px 210px at 430px 280px,rgba(238,232,220,.95),rgba(238,232,220,0) 100%),
    radial-gradient(ellipse 60px 160px at 100px 230px,rgba(200,180,140,.8),rgba(200,180,140,0) 100%),
    radial-gradient(ellipse 260px 70px at 200px 430px,rgba(150,55,45,.7),rgba(150,55,45,0) 100%),
    linear-gradient(180deg,#c9cbc8 0%,#bdb4a2 35%,#a48566 65%,#8a6e52 100%)" role="img" aria-label="Film still: bride and groom celebrating in a dry field with petals in the air">
    <svg class="play" viewBox="0 0 76 76"><circle cx="38" cy="38" r="38" fill="rgba(255,255,255,.18)"/><path d="M31 25 L52 38 L31 51 Z" fill="none" stroke="#fff" stroke-width="2"/></svg>
  </div>
  <div class="abs film-label" style="left:190px;top:2083px">
    <span class="num">03.</span>
    <span class="names"><span class="couple">Sienna &amp; Joel</span><span class="venue">Villa Colletta, Umbria, Italy</span></span>
  </div>

  <div class="abs film" style="top:2129px;background:
    radial-gradient(ellipse 100px 150px at 110px 290px,rgba(215,180,160,.9),rgba(215,180,160,0) 100%),
    radial-gradient(ellipse 110px 200px at 560px 250px,rgba(225,215,205,.9),rgba(225,215,205,0) 100%),
    radial-gradient(ellipse 140px 170px at 360px 200px,rgba(232,190,70,.95),rgba(232,190,70,0) 100%),
    radial-gradient(ellipse 140px 60px at 330px 430px,rgba(150,120,110,.7),rgba(150,120,110,0) 100%),
    linear-gradient(180deg,#8fb4d6 0%,#5f7f45 35%,#7a8a4e 65%,#9aa4a8 100%)" role="img" aria-label="Film still: laughing bride and groom in front of a yellow house">
    <svg class="play" viewBox="0 0 76 76"><circle cx="38" cy="38" r="38" fill="rgba(255,255,255,.18)"/><path d="M31 25 L52 38 L31 51 Z" fill="none" stroke="#fff" stroke-width="2"/></svg>
  </div>
  <div class="abs film-label" style="left:190px;top:2587px">
    <span class="num">04.</span>
    <span class="names"><span class="couple">Rosa &amp; Declan</span><span class="venue">Ashcombe Manor, Leicestershire</span></span>
  </div>

  <div class="abs film" style="top:2633px;background:
    radial-gradient(ellipse 90px 120px at 260px 120px,rgba(215,175,150,.85),rgba(215,175,150,0) 100%),
    radial-gradient(ellipse 100px 130px at 470px 170px,rgba(190,145,115,.85),rgba(190,145,115,0) 100%),
    radial-gradient(ellipse 140px 160px at 560px 360px,rgba(240,238,232,.95),rgba(240,238,232,0) 100%),
    radial-gradient(ellipse 120px 170px at 250px 340px,rgba(30,32,44,.95),rgba(30,32,44,0) 100%),
    linear-gradient(90deg,#7b5f50 0%,#5a4438 20%,#24252c 45%,#1a1a1e 75%,#2c2a2c 100%)" role="img" aria-label="Film still: smiling newlyweds leaving a church under white petals">
    <svg class="play" viewBox="0 0 76 76"><circle cx="38" cy="38" r="38" fill="rgba(255,255,255,.18)"/><path d="M31 25 L52 38 L31 51 Z" fill="none" stroke="#fff" stroke-width="2"/></svg>
  </div>
  <div class="abs film-label" style="left:190px;top:3091px">
    <span class="num">05.</span>
    <span class="names"><span class="couple">Maya &amp; Lewis</span><span class="venue">The Old Mill, Durham</span></span>
  </div>

  <div class="abs load-more"><span>LOAD MORE</span></div>

  <section class="abs testimonial"></section>
  <p class="abs quote"><span class="q">“</span> Sed ut perspiciatis unde omnis iste natus error sit voluptatem accusantium doloremque laudantium, totam rem aperiam, eaque ipsa quae ab illo inventore veritatis et quasi architecto beatae vitae dicta sunt explicabo <span class="q">”</span></p>
  <svg class="abs arrow" style="left:456px" width="22" height="10" viewBox="0 0 22 10"><path d="M21 5H1M5 1 1 5l4 4" fill="none" stroke="#c9c9c9" stroke-width="1"/></svg>
  <div class="abs avatar" role="img" aria-label="Portrait of the reviewing couple"></div>
  <svg class="abs arrow" style="left:722px" width="22" height="10" viewBox="0 0 22 10"><path d="M1 5h20M17 1l4 4-4 4" fill="none" stroke="#c9c9c9" stroke-width="1"/></svg>
  <div class="abs reviewer">OLIVER BRANTLEY</div>

  <div class="abs feature-media" role="img" aria-label="Video still of a bohemian couple celebrating outdoors">
    <svg class="abs" style="left:185px;top:103px" width="76" height="76" viewBox="0 0 76 76"><circle cx="38" cy="38" r="38" fill="rgba(255,255,255,.18)"/><path d="M31 25 L52 38 L31 51 Z" fill="none" stroke="#fff" stroke-width="2"/></svg>
  </div>
  <h2 class="abs feature-title">Want Something a<br>More Funky?</h2>
  <p class="abs feature-text">If you are a couple who prefers something a bit different to the styles above then why not go for our alternative option.</p>
  <div class="abs feature-link">SEND US MESSAGE</div>

  <section class="abs cta"></section>
  <div class="abs cta-text">Start your project with us</div>
  <div class="abs cta-btn">Get Started Now!</div>
</main>

<footer>
  <div class="abs footer"></div>
  <div class="abs footer-brand">BMRT</div>
  <div class="abs" style="left:344px;top:4303px">
    <div class="f-head">CONTACT US</div>
    <div class="f-main">Call Us. <span class="hl">+44 7700 900123</span></div>
    <div class="f-sub">e. hello@bmrtfilms.co.uk</div>
  </div>
  <div class="abs" style="left:677px;top:4303px">
    <div class="f-head">GET IN TOUCH</div>
    <div class="f-main">NE46 1XY Hexham</div>
    <div class="f-sub">Tynedale United Kingdom</div>
  </div>
  <div class="abs badge" aria-label="Featured badge"></div>
  <svg class="abs" style="left:1153px;top:4290px" width="16" height="20" viewBox="0 0 16 20"><path d="M8 19V1M2 7l6-6 6 6" fill="none" stroke="#a38d58" stroke-width="1.5"/></svg>
  <div class="abs divider"></div>
  <div class="abs copyright">2020 © BMRT Wedding Films. All Rights Reserved.</div>
  <div class="abs social" style="left:940px" aria-label="Social link"></div>
  <div class="abs social" style="left:979px" aria-label="Social link"></div>
  <div class="abs social" style="left:1017px" aria-label="Social link"></div>
</footer>

</body>
</html>
```